Card design for orthopaedic surgeons working as The Brightwater Joint Centre

Business cards, letterhead

Colors

Designer to choose colors to be used in the design.

Requirements
Must have
• Late addition.
• Cards letterhead must have logos of
• Crestmoor Lindell College of Surgeons
• Varenwood Bone Health Association
Nice to have
• Back of card to have space for appointment time to be added by hand and some blank space for writing incidental other notes.

```html
<!DOCTYPE html>
<html lang="en">
<head>
<meta charset="utf-8">
<title>The Brightwater Joint Centre – Business Card</title>
<link rel="stylesheet" href="https://fonts.googleapis.com/css2?family=Signika:wght@300;400;500&display=swap">
<style>
  :root {
    --navy: #052f49;
    --sky: #33aefc;
    --white: #ffffff;
    --backdrop: #ecebe8;
  }
  * { margin: 0; padding: 0; box-sizing: border-box; }
  html, body {
    width: 1125px; height: 1200px; overflow: hidden;
    background: var(--backdrop);
    font-family: "Signika", Arial, sans-serif;
  }
  .canvas { position: relative; width: 1125px; height: 1200px; }
  .card {
    position: absolute; left: 171px; width: 826px; height: 471px;
    border-radius: 26px; overflow: hidden;
    box-shadow: 0 3px 8px rgba(0,0,0,0.25);
  }
  .card--front { top: 106px; background: var(--white); }
  .card--back { top: 639px; background: var(--sky); }
  .front-panel { position: absolute; inset: 0; }
  .contact {
    position: absolute; left: 48px; top: 102px; color: var(--white);
    font-weight: 300;
  }
  .contact__name {
    font-size: 27px; font-weight: 500; color: var(--sky);
    letter-spacing: 0.5px; line-height: 1.1;
  }
  .contact__role { font-size: 17px; margin-top: 2px; }
  .contact__address { font-size: 17px; line-height: 23px; margin-top: 18px; }
  .contact__list { list-style: none; margin-top: 20px; font-size: 17px; line-height: 23.5px; }
  .contact__list li { display: flex; align-items: center; gap: 10px; }
  .contact__list svg { width: 15px; height: 15px; fill: var(--sky); flex: none; }
  .wordmark {
    position: absolute; left: 420px; width: 370px; top: 230px; text-align: center;
    font-size: 23px; font-weight: 400; color: var(--navy); white-space: nowrap;
  }
  .back-web {
    position: absolute; left: 0; right: 0; top: 392px; text-align: center;
    color: var(--white); font-size: 17px; font-weight: 300;
    letter-spacing: 14px; padding-left: 14px;
  }
</style>
</head>
<body>
<main class="canvas">
  <section class="card card--front">
    <svg class="front-panel" viewBox="0 0 826 471" width="826" height="471" aria-hidden="true">
      <path d="M0 0 H400 C358 45 332 110 352 180 C374 262 434 322 422 392 C414 432 390 458 362 471 H0 Z" fill="var(--sky)"/>
      <path d="M0 0 H394 C352 42 325 110 345 180 C366 260 426 320 415 390 C408 430 385 456 354 471 H0 Z" fill="var(--white)"/>
      <path d="M0 0 H391 C348 40 318 110 338 180 C358 260 418 320 408 390 C401 430 378 455 348 471 H0 Z" fill="var(--navy)"/>
      <path d="M356 280 C395 350 396 430 342 471" fill="none" stroke="var(--white)" stroke-width="2"/>
    </svg>
    <div class="contact">
      <h1 class="contact__name">DANIEL HARTLEY</h1>
      <p class="contact__role">President</p>
      <p class="contact__address">2140 Larkspur Road<br>Fairhaven, Oregon 97415</p>
      <ul class="contact__list">
        <li><svg viewBox="0 0 16 16"><path d="M3 1l3 3-1.5 2c1 2 2.5 3.5 4.5 4.5L11 9l3 3-2 3C6 14 2 10 1 3z"/></svg>555-201-4471</li>
        <li><svg viewBox="0 0 16 16"><path d="M4 0h8v16H4zM5.5 2v10h5V2z"/></svg>555-318-6620</li>
        <li><svg viewBox="0 0 16 16"><path d="M4 1h8v4H4zM1 6h14v7H1zM4 11h8v4H4z"/></svg>555-409-7735</li>
        <li><svg viewBox="0 0 16 16"><path d="M1 3h14v10H1zM2 4l6 5 6-5v1l-6 5-6-5z"/></svg>daniel@brightwaterjoint.com</li>
        <li><svg viewBox="0 0 16 16"><circle cx="8" cy="8" r="7"/></svg>www.brightwaterjoint.com</li>
      </ul>
    </div>
    <p class="wordmark">The Brightwater Joint Centre</p>
  </section>

  <section class="card card--back">
    <p class="back-web">WWW.BRIGHTWATERJOINT.COM</p>
  </section>
</main>
</body>
</html>
```